2014 Liberty Crown Falcon SET MS70 QRV

Its a four coin gold set $50, $25, $10, $5 Denominations QRV Early Releases or WMTB First Strikes , Free shipping with offer code KPL-472, Checks, Money Orders, Bank wires Always Welcome, Zorba, Feltopay, Wanderly, Global Trevvix, Members of QRV, WMTB, Lone Prairie Commerce League,RTQ A Plus, Put logos for QRV, WMTB, Lone Prairie commerce League, and logos for credit cards. Limited Time offer 4,100 while supplies last, Prices could change do to gold prices going up or down. 1-888-517-2093 Company name The Silver Ridge Mint House company motto "The Steady Bullion Keeper" Protect your money today in gold. We Buy Sell and Trade Daily. No shotgun approach, no high pressure sales, evaluate your coins for free, we are there to help you, business done the old fashioned way. One of the largest collection of modern and antique coins available in the world. Coins from $20 to Millions Address: The Silver Ridge Mint House, 2860 Juniper Blvd Suite C, Dell Harrow Texas, 77390

```html
<!DOCTYPE html>
<html lang="en">
<head>
<meta charset="utf-8">
<title>The Silver Ridge Mint House – Postcard</title>
<link href="https://fonts.googleapis.com/css2?family=Arimo:wght@400;700&family=Oswald:wght@400;500;600&family=Roboto+Condensed:wght@400;700&display=swap" rel="stylesheet">
<style>
  :root{
    --page:#d9dadd;
    --ink-black:#1c1c1c;
    --red-deep:#5e0a0c;
    --red-mid:#9c1418;
    --red-light:#c8262a;
    --gold:#e3b54a;
    --gold-deep:#c8902c;
    --white:#ffffff;
    --cream:#efd9cf;
    --cream-edge:#e4c3b6;
    --photo-a:#8a8e93;
    --photo-b:#d8d9da;
    --gold-coin:#b88a2c;
  }
  *{box-sizing:border-box;margin:0;padding:0}
  html,body{width:925px;height:1200px;overflow:hidden;background:var(--page)}
  body{position:relative;font-family:"Roboto Condensed",sans-serif;color:var(--white)}

  .card{position:absolute;box-shadow:0 4px 10px rgba(0,0,0,.35);overflow:hidden}
  .silk{background:
      radial-gradient(ellipse 60% 30% at 30% 45%,rgba(230,70,70,.55),transparent 70%),
      radial-gradient(ellipse 70% 25% at 70% 75%,rgba(220,60,60,.45),transparent 70%),
      linear-gradient(160deg,var(--red-deep) 0%,var(--red-mid) 35%,var(--red-light) 55%,var(--red-mid) 75%,var(--red-deep) 100%)}

  /* Front */
  .card-front{left:71px;top:65px;width:687px;height:525px}
  .front-header{position:absolute;left:0;top:0;width:100%;height:126px;background:linear-gradient(#2a2a2a,var(--ink-black));text-align:center;border-bottom:3px solid var(--gold-deep)}
  .brand-name{font-family:"Arimo",sans-serif;font-weight:700;font-size:47px;padding-top:14px;letter-spacing:-.5px}
  .brand-motto{font-family:"Oswald",sans-serif;font-weight:500;font-size:29px;color:var(--gold);margin-top:2px}
  .intro{position:absolute;left:17px;top:135px;width:660px;font-weight:700;font-size:17.5px;line-height:1.35}
  .coin-photo{position:absolute;left:17px;top:198px;width:280px;height:262px;border-radius:6px;background:linear-gradient(135deg,var(--photo-b),var(--photo-a));display:grid;grid-template-columns:1fr 1fr;gap:8px;padding:12px}
  .coin-photo span{border-radius:4px;background:radial-gradient(circle at 50% 62%,var(--gold-coin) 0 24%,#eef0f1 26%)}
  .ribbon{position:absolute;left:30px;top:455px;width:300px;height:40px;background:linear-gradient(var(--red-light),var(--red-deep));border-top:2px solid var(--gold);border-bottom:2px solid var(--gold);transform:rotate(-2deg);font-family:"Oswald",sans-serif;font-size:17px;color:var(--gold);text-align:center;line-height:36px}
  .offer{position:absolute;left:380px;top:195px;width:300px}
  .offer h2{font-family:"Oswald",sans-serif;font-weight:400;font-size:25px;margin-bottom:10px}
  .offer ul{list-style:none;font-family:"Oswald",sans-serif;font-size:20px;line-height:1.35}
  .offer li::before{content:"•";margin:0 10px 0 4px}
  .help{position:absolute;left:380px;top:335px;width:300px;font-family:"Oswald",sans-serif}
  .help h3{font-weight:600;font-size:25px;letter-spacing:-.3px}
  .help p{font-size:20px;margin-top:-2px}
  .fine{position:absolute;left:380px;top:400px;width:300px;text-align:center;font-size:10.5px;line-height:1.45}
  .front-phone{position:absolute;left:380px;top:470px;width:300px;display:flex;justify-content:center;align-items:center;gap:8px;font-family:"Oswald",sans-serif;font-size:24px;color:var(--gold)}

  /* Back */
  .card-back{left:161px;top:617px;width:689px;height:525px;background:linear-gradient(135deg,var(--cream),var(--cream-edge))}
  .back-panel{position:absolute;left:0;top:0;width:379px;height:100%;padding:0 18px}
  .back-name{font-family:"Arimo",sans-serif;font-weight:700;font-size:26px;margin-top:34px}
  .back-motto{margin:8px -18px 0;padding:4px 0 6px 40px;font-family:"Oswald",sans-serif;font-weight:500;font-size:20px;color:var(--gold);background:linear-gradient(90deg,rgba(0,0,0,.55),rgba(0,0,0,.2));border-top:1px solid var(--gold-deep);border-bottom:1px solid var(--gold-deep)}
  .set-title{text-align:center;font-family:"Oswald",sans-serif;font-size:21px;color:var(--gold);line-height:1.3;margin-top:20px}
  .set-details{font-weight:700;font-size:10.5px;line-height:1.55;margin-top:18px}
  .pay-row{display:flex;gap:12px;margin-top:16px}
  .pay-mark{display:flex;align-items:center;gap:4px;background:var(--white);color:var(--ink-black);font-weight:700;font-size:10px;padding:5px 6px;border-radius:2px}
  .pay-mark i{width:7px;height:7px;background:var(--red-mid)}
  .divider{border-top:1px dashed rgba(255,255,255,.5);margin:16px -18px 10px}
  .members-label{font-weight:700;font-size:11px}
  .member-row{display:flex;gap:10px;margin-top:6px;align-items:center}
  .member-mark{background:var(--white);color:var(--ink-black);font-weight:700;font-size:11px;padding:8px 10px}
  .member-badge{width:28px;height:34px;background:var(--white)}
  .contact{font-weight:700;font-size:12.5px;line-height:1.9;margin-top:30px}
  .web{font-family:"Oswald",sans-serif;font-weight:500;font-size:21px;color:var(--gold);margin-top:16px}
</style>
</head>
<body>

<section class="card card-front silk">
  <header class="front-header">
    <h1 class="brand-name">The Silver Ridge Mint House</h1>
    <p class="brand-motto">The Steady Bullion Keeper</p>
  </header>
  <p class="intro">One of the largest collection of modern and antique coins available in the world.<br>Coins from $20 to Millions</p>
  <div class="coin-photo" role="img" aria-label="Four graded Liberty Crown Falcon gold coins in slabs"><span></span><span></span><span></span><span></span></div>
  <div class="ribbon">Protect Your Money Today In Gold</div>
  <div class="offer">
    <h2>We Buy Sell and Trade Daily</h2>
    <ul><li>No shotgun approach</li><li>No high pressure sales</li><li>Evaluate your coins for free</li></ul>
  </div>
  <div class="help">
    <h3>WE ARE THERE TO HELP YOU</h3>
    <p>Business Done The Old Fashioned Way</p>
  </div>
  <p class="fine">Limited Time offer 4,100 while supplies last,<br>Prices could change do to gold prices going up or down.</p>
  <p class="front-phone">
    <svg width="18" height="24" viewBox="0 0 18 24" aria-hidden="true"><path d="M5 1 L8 7 L5.5 9 Q7 15 11 18 L13.5 16 L17 21 L14 23 Q4 20 2 6 Q2 2 5 1Z" fill="currentColor"/></svg>
    1-888-517-2093
  </p>
</section>

<section class="card card-back">
  <div class="back-panel silk">
    <h1 class="back-name">The Silver Ridge Mint House</h1>
    <p class="back-motto">The Steady Bullion Keeper</p>
    <p class="set-title">FOUR GOLD COIN SET<br>$50, $25, $10, $5</p>
    <p class="set-details">Denominations QRV Early Releases or WMTB First Strikes ,<br>Free shipping with offer code KPL-472,<br>Checks, Money Orders, Bank wires Always Welcome,</p>
    <div class="pay-row">
      <span class="pay-mark"><i></i>Zorba</span>
      <span class="pay-mark"><i></i>Feltopay</span>
      <span class="pay-mark"><i></i>Wanderly</span>
      <span class="pay-mark"><i></i>Global Trevvix</span>
    </div>
    <div class="divider"></div>
    <p class="members-label">Members of:</p>
    <div class="member-row">
      <span class="member-mark">QRV</span>
      <span class="member-mark">WMTB</span>
      <span class="member-badge" role="img" aria-label="Lone Prairie Commerce League member badge"></span>
      <span class="member-badge" role="img" aria-label="RTQ A Plus badge"></span>
    </div>
    <p class="contact">Phone: 1-888-517-2093<br>Address: 2860 Juniper Blvd Suite C, Dell Harrow Texas, 77390</p>
    <p class="web">www.silverridgeminthouse.us</p>
  </div>
</section>

</body>
</html>
```